The Vantor Codex Book Cover

"The Vantor Codex" is a book I wrote with the slogan "Unlock Performance, Spark Engagement: Master the Art of Building Winning Cultures in Today's Hybrid World". The book is designed around a methodology that's mine and that I attached. I would love to see the graphic of the methodology integrated in the design in a very subtle way. Use colors from the model but the book cover should be catchy, modern and engaging to the eye.
Overall the book is about three key elements towards success:
- (Self) Directions (purpose)
- Human experience (people and psychological safety)
- Maximize engagement
The methodology is a FLOW so flow is something that could be incorporated as well in the concept.
Low design quality
Managers and Teams

```html
<!DOCTYPE html>
<html lang="en">
<head>
<meta charset="utf-8">
<title>The Vantor Codex — Book Cover</title>
<link rel="stylesheet" href="https://fonts.googleapis.com/css2?family=DM+Serif+Display:ital@0;1&family=Oswald:wght@200;500;700&display=swap">
<style>
  :root {
    --cover-bg: #215d76;
    --ink-white: #ffffff;
    --ink-cyan: #62f5ef;
    --tone-pink: #f0607a;
    --tone-plum: #6a4f86;
    --tone-gold: #f7c53f;
    --tone-olive: #c2b43a;
    --tone-aqua: #5fd3de;
  }
  * { margin: 0; padding: 0; box-sizing: border-box; }
  html, body { width: 933px; height: 1200px; overflow: hidden; background: var(--cover-bg); }
  .cover {
    position: relative;
    width: 933px;
    height: 1200px;
    background: var(--cover-bg);
    color: var(--ink-white);
    overflow: hidden;
  }
  .tagline {
    position: absolute;
    top: 88px;
    width: 264px;
    height: 38px;
    border-top: 3px solid var(--ink-white);
    border-bottom: 3px solid var(--ink-white);
    display: flex;
    align-items: center;
    justify-content: center;
    font-family: "Oswald", sans-serif;
    font-weight: 500;
    font-size: 17px;
    letter-spacing: 5.2px;
    text-transform: uppercase;
  }
  .tagline--left { left: 95px; }
  .tagline--right { left: 541px; }
  .title {
    position: absolute;
    left: 0;
    top: 0;
    width: 100%;
    font-family: "DM Serif Display", serif;
    text-align: center;
    line-height: 1;
  }
  .title__article {
    position: absolute;
    left: 0; width: 100%;
    top: 62px;
    font-style: italic;
    font-size: 92px;
    letter-spacing: -2px;
    color: var(--ink-white);
  }
  .title__main {
    position: absolute;
    left: 0; width: 100%;
    top: 128px;
    font-size: 172px;
    letter-spacing: -3px;
    color: var(--ink-white);
  }
  .title__accent {
    position: absolute;
    left: 0; width: 100%;
    top: 248px;
    font-size: 200px;
    letter-spacing: -4px;
    color: var(--ink-cyan);
  }
  .subtitle {
    position: absolute;
    left: 0; width: 100%;
    top: 460px;
    text-align: center;
    font-family: "Oswald", sans-serif;
    font-weight: 500;
    font-size: 33px;
    line-height: 46px;
    letter-spacing: -0.5px;
    text-transform: uppercase;
    transform: scaleY(1.05);
  }
  .methodology-art {
    position: absolute;
    left: 113px;
    top: 566px;
    width: 714px;
    height: 476px;
  }
  .author {
    position: absolute;
    left: 0; width: 100%;
    top: 1100px;
    text-align: center;
    font-family: "Oswald", sans-serif;
    font-size: 66px;
    line-height: 1;
    letter-spacing: 30px;
    text-transform: uppercase;
    padding-left: 30px;
  }
  .author__first { font-weight: 200; margin-right: 46px; }
  .author__last { font-weight: 700; }
</style>
</head>
<body>
  <main class="cover">
    <div class="tagline tagline--left">Unlock Performance</div>
    <div class="tagline tagline--right">Spark Engagement</div>

    <h1 class="title">
      <span class="title__article">The</span>
      <span class="title__main">Vantor</span>
      <span class="title__accent">Codex</span>
    </h1>

    <p class="subtitle">Master the art of building winning<br>cultures in today's hybrid world</p>

    <svg class="methodology-art" viewBox="0 0 714 476" role="img" aria-label="Illustration of a glowing methodology wheel with compass, team of figures held in an open hand, and a flowing loop of pink, purple, gold and aqua segments">
      <defs>
        <radialGradient id="art-left" cx="0.5" cy="0.5" r="0.5">
          <stop offset="0" stop-color="var(--tone-gold)"/>
          <stop offset="0.55" stop-color="var(--tone-pink)"/>
          <stop offset="1" stop-color="var(--tone-plum)" stop-opacity="0.7"/>
        </radialGradient>
        <radialGradient id="art-right" cx="0.5" cy="0.45" r="0.5">
          <stop offset="0" stop-color="#ffffff"/>
          <stop offset="0.35" stop-color="var(--tone-olive)"/>
          <stop offset="1" stop-color="var(--tone-aqua)" stop-opacity="0.75"/>
        </radialGradient>
        <radialGradient id="art-glow" cx="0.5" cy="0.5" r="0.5">
          <stop offset="0" stop-color="#7fc6da" stop-opacity="0.35"/>
          <stop offset="1" stop-color="#7fc6da" stop-opacity="0"/>
        </radialGradient>
      </defs>
      <ellipse cx="357" cy="238" rx="357" ry="238" fill="url(#art-glow)"/>
      <circle cx="204" cy="238" r="180" fill="url(#art-left)"/>
      <circle cx="484" cy="230" r="180" fill="url(#art-right)"/>
    </svg>

    <p class="author"><span class="author__first">Ruben</span><span class="author__last">Holter</span></p>
  </main>
</body>
</html>
```